Logo Tweaks & Stationery Design Project for Energy Management Co

We are a specialist metering company trading for over 60 years and have recently developed GPRS metering infrastructure & monitoring services. For more information please see http://www.kestrel-vale.example/remote-meter-reading.html

Due to the success of this system it’s become necessary to open a new company “Brightwell Gauge Ltd” and this project is for relevant stationary designs for our documents.

I need something modern and clear to match our new logo style. Feel free to play around with the colors and tweak the logo if you like.

Maybe with some line chart animation on the header relating to our online services. ( See inspiration file )

Thanks
Derek

Target Market(s)

Renewable Energy Generation Monitoring, Energy Management, Remote Monitoring and Tennant Billing.

Industry/Entity Type

It Company

Requirements
Nice to have
• 100% Carbon neutral hosting
Should not have
• "Clip-Art" should not be used.

```html
<!DOCTYPE html>
<html lang="en">
<head>
<meta charset="utf-8">
<title>Brightwell Gauge – Stationery</title>
<link rel="stylesheet" href="https://fonts.googleapis.com/css2?family=Michroma&family=EB+Garamond&display=swap">
<style>
  :root {
    --page-bg: #ece6da;
    --brand-blue: #2a3a98;
    --brand-red: #be1e2d;
    --band-grey: #6b6b6d;
    --paper: #ffffff;
    --edge: #8a8a8a;
    --label: #1a1a1a;
    --brand-font: "Michroma", sans-serif;
    --label-font: "EB Garamond", serif;
  }
  html, body { margin: 0; padding: 0; overflow: hidden; }
  .canvas {
    position: relative;
    width: 1071px;
    height: 1200px;
    background: var(--page-bg);
    overflow: hidden;
  }
  .piece { position: absolute; display: block; }
  .letterhead { left: 117px; top: 337px; filter: drop-shadow(2px 3px 3px rgba(0,0,0,.35)); }
  .envelope-back { left: 642px; top: 137px; }
  .envelope-front-blue { left: 661px; top: 458px; }
  .envelope-front-red { left: 661px; top: 761px; }
  .label {
    position: absolute;
    margin: 0;
    font-family: var(--label-font);
    font-size: 24px;
    color: var(--label);
    line-height: 1;
  }
  .label--small { font-size: 15px; }
  .brand-name { font-family: var(--brand-font); fill: var(--brand-blue); }
</style>
</head>
<body>
<main class="canvas">

  <!-- Letterhead -->
  <svg class="piece letterhead" width="352" height="496" viewBox="0 0 352 496" aria-label="Letterhead">
    <rect x="0" y="0" width="352" height="496" fill="var(--paper)"/>
    <rect x="0" y="0" width="352" height="64" fill="var(--brand-red)"/>
    <text class="brand-name" x="12" y="41" font-size="18">BRIGHTWELL GAUGE</text>
    <rect x="0" y="477" width="352" height="19" fill="var(--band-grey)"/>
    <text class="brand-name" x="176" y="491" font-size="10" text-anchor="middle" letter-spacing="1">BRIGHTWELL GAUGE</text>
  </svg>
  <p class="label label--small" style="left:125px; top:866px;">Letter Head</p>

  <!-- Envelope back -->
  <svg class="piece envelope-back" width="368" height="238" viewBox="0 0 368 238" aria-label="Envelope back">
    <rect x="0" y="66" width="368" height="172" fill="var(--paper)" stroke="var(--edge)" stroke-width="1"/>
    <polygon points="0,66 12,33 192,0 354,32 368,66" fill="var(--brand-blue)"/>
    <polyline points="0,66 172,103 368,66" fill="none" stroke="var(--edge)" stroke-width="1"/>
    <rect x="0" y="219" width="368" height="19" fill="var(--band-grey)"/>
    <text class="brand-name" x="184" y="233" font-size="10" text-anchor="middle" letter-spacing="1">BRIGHTWELL GAUGE</text>
  </svg>
  <p class="label" style="left:652px; top:380px;">Back</p>
  <p class="label" style="left:575px; top:437px;">Envelop</p>

  <!-- Envelope front, blue band -->
  <svg class="piece envelope-front-blue" width="367" height="238" viewBox="0 0 367 238" aria-label="Envelope front with blue band">
    <defs>
      <clipPath id="front-blue-body"><rect x="0" y="66" width="367" height="172"/></clipPath>
    </defs>
    <polygon points="0,66 13,33 192,0 354,32 367,66" fill="var(--paper)" stroke="var(--edge)" stroke-width="1"/>
    <rect x="0" y="66" width="367" height="172" fill="var(--paper)" stroke="var(--edge)" stroke-width="1"/>
    <g clip-path="url(#front-blue-body)">
      <rect x="0" y="201" width="367" height="37" fill="var(--brand-blue)"/>
      <circle cx="352" cy="182" r="72" fill="var(--brand-blue)"/>
      <circle cx="354" cy="186" r="66" fill="var(--brand-red)"/>
    </g>
    <text class="brand-name" x="12" y="192" font-size="17">BRIGHTWELL GAUGE</text>
  </svg>
  <p class="label" style="left:662px; top:704px;">Front</p>
  <p class="label" style="left:575px; top:741px;">Envelop</p>

  <!-- Envelope front, red band -->
  <svg class="piece envelope-front-red" width="367" height="238" viewBox="0 0 367 238" aria-label="Envelope front with red band">
    <defs>
      <clipPath id="front-red-body"><rect x="0" y="66" width="367" height="172"/></clipPath>
    </defs>
    <polygon points="0,66 13,33 192,0 354,32 367,66" fill="var(--paper)" stroke="var(--edge)" stroke-width="1"/>
    <rect x="0" y="66" width="367" height="172" fill="var(--paper)" stroke="var(--edge)" stroke-width="1"/>
    <g clip-path="url(#front-red-body)">
      <rect x="0" y="201" width="367" height="37" fill="var(--brand-red)"/>
      <circle cx="352" cy="180" r="72" fill="var(--brand-red)"/>
      <circle cx="354" cy="184" r="66" fill="var(--brand-blue)"/>
    </g>
    <text class="brand-name" x="12" y="192" font-size="17">BRIGHTWELL GAUGE</text>
  </svg>
  <p class="label" style="left:676px; top:1017px;">Front</p>

</main>
</body>
</html>
```